Clear Plastic Card Design

I am looking to have a business card designed from my logo icon. I am looking to match the style of a different business card I have attached in the files.
Looking for a card that is plastic, with layers of transparency in the shape of my logo icon (also attached in the files) - not a circle like the other card. The winning design will incorporate the red icon logo on the front and back and include the charity's name, "Light for the Weary Souls" in the same or similar font, as well as an email and phone number. For now, use the email: email@lightfortheweary-mail.org and the phone number 555-382-7194.
We like how the sample business card has transparency, partial and full opacity layers and a matching color scheme. Files will need to be in vector so that our business card printing company can work with it.
UPDATE:
We've some excellent designs in, thank you everyone! I got an early review from the owner, and he requested a minor redirect to find his perfect design. He wants the design to stand out by NOT being a rectangle. Try instead a circle, square, or best yet - something that falls in the outline of the logo icon, either fully or partially. Thank you, everyone!
Light for the Weary Souls text should be incorporated as well as a phone and email.

```html
<!DOCTYPE html>
<html lang="en">
<head>
<meta charset="utf-8">
<title>Light for the Weary Souls – Round Card</title>
<link href="https://fonts.googleapis.com/css2?family=Oswald:wght@500&family=Poppins:wght@700&display=swap" rel="stylesheet">
<style>
  :root {
    --backdrop: #e8e4df;
    --card-dark: #2a2a2a;
    --card-dark-ink: #0e0e0e;
    --card-light: #f2f0ee;
    --ink: #111111;
    --brand-red: #e0241b;
  }
  html, body {
    margin: 0;
    padding: 0;
    overflow: hidden;
  }
  .canvas {
    position: relative;
    width: 1200px;
    height: 800px;
    background: var(--backdrop);
    overflow: hidden;
  }
  .card {
    position: absolute;
    width: 476px;
    height: 476px;
    border-radius: 50%;
    overflow: hidden;
  }
  .card--back {
    left: 96px;
    top: 236px;
    background: var(--card-dark);
    display: flex;
    align-items: center;
    justify-content: center;
  }
  .back-name {
    margin: 0;
    font-family: 'Poppins', sans-serif;
    font-weight: 700;
    font-size: 54px;
    line-height: 1.1;
    text-align: center;
    text-transform: uppercase;
    color: var(--card-dark-ink);
  }
  .card--front {
    left: 600px;
    top: 234px;
    background: var(--card-light);
  }
  .front-brand {
    position: absolute;
    top: 70px;
    left: 0;
    width: 100%;
    display: flex;
    align-items: center;
    justify-content: center;
    gap: 12px;
  }
  .brand-dot {
    width: 22px;
    height: 22px;
    border-radius: 50%;
    background: var(--brand-red);
  }
  .brand-name {
    margin: 0;
    font-family: 'Poppins', sans-serif;
    font-weight: 700;
    font-size: 26px;
    line-height: 1.15;
    color: var(--brand-red);
  }
  .contact {
    position: absolute;
    left: 0;
    width: 100%;
    display: flex;
    align-items: center;
    justify-content: center;
    gap: 8px;
    font-family: 'Oswald', sans-serif;
    font-weight: 500;
    color: var(--ink);
    white-space: nowrap;
  }
  .contact--phone { top: 204px; font-size: 32px; }
  .contact--email { top: 253px; font-size: 23px; text-transform: uppercase; }
  .contact__domain { color: var(--brand-red); }
  .contact__icon { flex: none; }
  .front-title {
    position: absolute;
    top: 322px;
    left: 0;
    width: 100%;
    margin: 0;
    font-family: 'Poppins', sans-serif;
    font-weight: 700;
    font-size: 31px;
    line-height: 1.15;
    text-align: center;
    text-transform: uppercase;
    color: var(--brand-red);
  }
  .front-cap {
    position: absolute;
    left: 160px;
    top: 436px;
    width: 156px;
    height: 80px;
    border-radius: 78px 78px 0 0;
    background: var(--brand-red);
  }
</style>
</head>
<body>
<main class="canvas">
  <section class="card card--back" aria-label="Card back">
    <p class="back-name">Light for<br>the Weary<br>Souls</p>
  </section>

  <section class="card card--front" aria-label="Card front">
    <div class="front-brand">
      <span class="brand-dot"></span>
      <p class="brand-name">Light for the<br>Weary Souls</p>
    </div>

    <div class="contact contact--phone">
      <svg class="contact__icon" width="32" height="26" viewBox="0 0 32 26" aria-hidden="true">
        <path d="M2 9 Q16 -1 30 9 L27 13 L22 11 L21 7 Q16 5 11 7 L10 11 L5 13 Z" fill="var(--brand-red)"/>
        <path d="M6 14 L11 10 L21 10 L26 14 L28 25 L4 25 Z" fill="var(--brand-red)"/>
        <circle cx="16" cy="18" r="4" fill="none" stroke="var(--card-light)" stroke-width="1.6"/>
      </svg>
      <span>555-382-7194</span>
    </div>

    <div class="contact contact--email">
      <svg class="contact__icon" width="30" height="24" viewBox="0 0 30 24" aria-hidden="true">
        <path d="M29 1 L1 12 L9 14 Z" fill="var(--brand-red)"/>
        <path d="M29 1 L11 15 L13 23 L16 17 L23 20 Z" fill="var(--brand-red)"/>
      </svg>
      <span>email<span class="contact__domain">@lightfortheweary-mail</span>.org</span>
    </div>

    <h1 class="front-title">Light for the<br>Weary Souls</h1>

    <div class="front-cap"></div>
  </section>
</main>
</body>
</html>
```